Veltrano.co - Polar Expeditions Specialists

We need a modern, visually striking business card for Veltrano.co, a company specialized in selling expedition cruises to the most remote regions on Earth, with a focus on the Arctic and Antarctica. The design should instantly communicate that the cardholder is an expert in polar travel. Use clean, premium aesthetics with cool tones like icy blue and white, possibly incorporating polar imagery (ice, glaciers, penguins, etc.)

Attached the logo

Contact Information for Business Card

Feels high-end and trustworthy.. Visually memorable — encourages people to keep it

Colors
0054AA
0677BA
7BADD7
CADEEF
E8F1F8

Requirements
Must have
• ice, glaciers, penguins, montains
Nice to have
• modern, transparente,

```html
<!DOCTYPE html>
<html lang="en">
<head>
<meta charset="utf-8">
<title>Veltrano.co Business Card</title>
<link href="https://fonts.googleapis.com/css2?family=Poppins:wght@400;500;600;700&display=swap" rel="stylesheet">
<style>
  :root {
    --page-bg: #e6eaef;
    --brand-blue: #3070b0;
    --deep-navy: #13132b;
    --card-white: #ffffff;
    --text-light: #f2f4f8;
  }
  * { box-sizing: border-box; margin: 0; padding: 0; }
  html, body { width: 1200px; height: 900px; overflow: hidden; }
  body {
    background: var(--page-bg);
    font-family: "Poppins", sans-serif;
    position: relative;
  }
  .card {
    position: absolute;
    left: 320px;
    width: 560px;
    height: 320px;
    border-radius: 22px;
    overflow: hidden;
    box-shadow: 0 10px 30px rgba(20, 30, 60, 0.18);
  }
  .card-front {
    top: 80px;
    background: var(--brand-blue);
    display: flex;
    flex-direction: column;
    align-items: center;
    justify-content: center;
    color: var(--card-white);
  }
  .card-back { top: 500px; background: var(--deep-navy); }
  .card-back .backdrop { position: absolute; inset: 0; width: 100%; height: 100%; }

  .brand {
    display: flex;
    align-items: center;
    gap: 12px;
    white-space: nowrap;
  }
  .brand-dot {
    width: 16px; height: 16px; border-radius: 50%;
    background: currentColor;
    flex: none;
  }
  .brand-name {
    font-weight: 700;
    font-size: 52px;
    line-height: 1;
    letter-spacing: 0.5px;
  }
  .brand-tagline {
    margin-top: 8px;
    font-weight: 600;
    font-size: 16px;
    letter-spacing: 0.3px;
    white-space: nowrap;
  }

  .contact {
    position: absolute;
    left: 44px;
    top: 58px;
    color: var(--text-light);
  }
  .contact .accent-bar {
    position: absolute;
    left: -26px; top: 4px;
    width: 4px; height: 34px;
    background: var(--brand-blue);
  }
  .person-name {
    color: var(--brand-blue);
    font-weight: 700;
    font-size: 26px;
    line-height: 1.1;
  }
  .person-role { font-size: 13px; margin-top: 2px; }
  .address { font-size: 13px; line-height: 1.45; margin-top: 16px; }
  .contact-list { list-style: none; margin-top: 10px; font-size: 13px; line-height: 1.6; }
  .contact-list li { display: flex; align-items: center; gap: 8px; }
  .contact-list svg { width: 12px; height: 12px; fill: var(--brand-blue); flex: none; }

  .back-brand {
    position: absolute;
    left: 322px;
    width: 222px;
    top: 130px;
    color: var(--brand-blue);
    display: flex;
    flex-direction: column;
    align-items: center;
  }
  .back-brand .brand { gap: 8px; }
  .back-brand .brand-dot { width: 10px; height: 10px; }
  .back-brand .brand-name { font-size: 30px; letter-spacing: 0; }
  .back-brand .brand-tagline { font-size: 11.5px; margin-top: 6px; letter-spacing: 0; }
</style>
</head>
<body>

  <section class="card card-front">
    <div class="brand">
      <span class="brand-dot"></span>
      <span class="brand-name">Veltrano.co</span>
    </div>
    <p class="brand-tagline">Polar Expeditions Specialists</p>
  </section>

  <section class="card card-back">
    <svg class="backdrop" viewBox="0 0 560 320" preserveAspectRatio="none" aria-hidden="true">
      <circle cx="620" cy="268" r="350" fill="var(--brand-blue)"/>
      <circle cx="640" cy="252" r="345" fill="var(--card-white)"/>
    </svg>

    <div class="contact">
      <span class="accent-bar"></span>
      <h1 class="person-name">Marlon Vesk</h1>
      <p class="person-role">CEO &amp; Founder</p>
      <p class="address">42 Harbor Crest Lane,<br>Lakewood, OR 97035 USA</p>
      <ul class="contact-list">
        <li>
          <svg viewBox="0 0 24 24"><path d="M6.6 10.8a15 15 0 0 0 6.6 6.6l2.2-2.2a1 1 0 0 1 1-.25 11.4 11.4 0 0 0 3.6.57 1 1 0 0 1 1 1V20a1 1 0 0 1-1 1A17 17 0 0 1 3 4a1 1 0 0 1 1-1h3.5a1 1 0 0 1 1 1c0 1.25.2 2.45.57 3.57a1 1 0 0 1-.25 1z"/></svg>
          +1.555.014.278
        </li>
        <li>
          <svg viewBox="0 0 24 24"><path d="M2 5h20v14H2z M2 5l10 8 10-8" /></svg>
          info@veltranomail.com
        </li>
        <li>
          <svg viewBox="0 0 24 24"><circle cx="12" cy="12" r="10"/></svg>
          www.veltranotravel.com
        </li>
      </ul>
    </div>

    <div class="back-brand">
      <div class="brand">
        <span class="brand-dot"></span>
        <span class="brand-name">Veltrano.co</span>
      </div>
      <p class="brand-tagline">Polar Expeditions Specialists</p>
    </div>
  </section>

</body>
</html>
```